Social Media App Needs PPT Template

We need a PowerPoint template for a new social media company based in the DC area called "Bold Ledger." We provide an interactive digital platform for executives to share actionable advice. We would like to see designs that use our orange logo color as an accent, but are mainly grey, white, and black. The final design should communicate clean, chic, modern, and professional.

Target Market(s)

Executives

Industry/Entity Type

Information Technology

Font styles to use
Sans Serif

Colors
f78f20
fbe7d2
ffffff
000000
e8e8e8
757575

Requirements
Must have
• My project must have title page and many options for the body of the ppt (graphs, tables, etc). It also needs to be easy to modify. I must have someone who is experienced in creating powerpoint templates.
Nice to have
• It would be nice to have a very modern and clean design that includes the logo on every page, but still leaves a lot of room for the content of the slide
Should not have
• My design project should not look to busy.

```html
<!DOCTYPE html>
<html lang="en">
<head>
<meta charset="utf-8">
<title>Bold Ledger – About Our Company</title>
<link rel="stylesheet" href="https://fonts.googleapis.com/css2?family=Lato:wght@300;400;700&display=swap">
<style>
  :root {
    --orange: #e8861a;
    --orange-light: #f0951f;
    --charcoal: #4a4a4a;
    --rule: #757575;
    --paper: #f4f4f4;
    --paper-glow: #ffffff;
    --text-dark: #4a4a4a;
    --white: #ffffff;
    --backdrop: #8f8f8f;
  }
  * { margin: 0; padding: 0; box-sizing: border-box; }
  html, body {
    width: 1200px; height: 960px; overflow: hidden;
    background: var(--backdrop);
    font-family: "Lato", sans-serif;
  }
  .stage { position: relative; width: 1200px; height: 960px; }
  .slide {
    position: absolute; left: 0; top: 30px;
    width: 1307px; height: 980px;
    transform: scale(0.9181); transform-origin: 0 0;
    background: radial-gradient(ellipse at 55% 35%, var(--paper-glow) 0%, var(--paper) 60%, #efefef 100%);
    overflow: hidden;
  }
  .header-shapes, .footer-shapes { position: absolute; left: 0; }
  .header-shapes { top: 0; }
  .footer-shapes { top: 920px; }
  .slide-title {
    position: absolute; left: 40px; top: 88px;
    font-weight: 300; font-size: 49px; color: var(--white);
    letter-spacing: 0.3px;
  }
  .brand {
    position: absolute; left: 1062px; top: 92px;
    display: flex; align-items: center; gap: 10px;
    color: var(--white); font-weight: 700; font-size: 27px;
  }
  .brand-dot { width: 18px; height: 18px; border-radius: 50%; background: var(--orange); }
  .data-table {
    position: absolute; left: 65px; top: 308px; width: 1189px;
    border-top: 2px solid #8a8a8a;
  }
  .table-head, .table-row { display: flex; align-items: center; }
  .table-head { height: 104px; padding-top: 8px; }
  .table-head .cell { font-size: 21px; font-weight: 700; color: var(--rule); }
  .table-row { height: 102px; color: var(--text-dark); }
  .table-row.is-dark { background: var(--charcoal); color: var(--white); }
  .row-label { width: 422px; padding-left: 126px; font-size: 25px; padding-top: 8px; }
  .cell { width: 253px; text-align: center; font-size: 38px; }
  .footer-text {
    position: absolute; left: 35px; top: 934px;
    font-size: 18px; color: #e6e6e6;
  }
  .footer-text .sep { margin: 0 8px; }
</style>
</head>
<body>
<main class="stage">
  <section class="slide">
    <svg class="header-shapes" width="1307" height="190" viewBox="0 0 1307 190" aria-hidden="true">
      <polygon points="1017,43 1307,43 1307,55 1005,55" fill="var(--orange)"/>
      <polygon points="0,61 990,61 885,163 0,163" fill="var(--orange)"/>
      <polygon points="790,61 990,61 940,110 740,110" fill="var(--orange-light)" opacity="0.55"/>
      <polygon points="1002,61 1307,61 1307,163 893,163" fill="var(--charcoal)"/>
      <polygon points="0,169 880,169 869,181 0,181" fill="var(--charcoal)"/>
    </svg>
    <h1 class="slide-title">About Our Company</h1>
    <div class="brand"><span class="brand-dot"></span>Bold Ledger</div>

    <div class="data-table">
      <div class="table-head">
        <span class="row-label"></span>
        <span class="cell">A</span><span class="cell">B</span><span class="cell">C</span>
      </div>
      <div class="table-row is-dark">
        <span class="row-label">Type 1</span>
        <span class="cell">20</span><span class="cell">30</span><span class="cell">40</span>
      </div>
      <div class="table-row">
        <span class="row-label">Type 2</span>
        <span class="cell">50</span><span class="cell">60</span><span class="cell">70</span>
      </div>
      <div class="table-row is-dark">
        <span class="row-label">Type 3</span>
        <span class="cell">80</span><span class="cell">90</span><span class="cell">100</span>
      </div>
    </div>

    <svg class="footer-shapes" width="1307" height="60" viewBox="0 0 1307 60" aria-hidden="true">
      <polygon points="0,7 372,7 333,46 0,46" fill="var(--charcoal)"/>
      <polygon points="380,7 1307,7 1307,46 341,46" fill="var(--orange)"/>
    </svg>
    <p class="footer-text">www.boldledger.com<span class="sep">|</span>Page 7</p>
  </section>
</main>
</body>
</html>
```